Updated Business Card Re-design (Logo Provided)

I am needing to update our business cards for our practice, Brightfield Care Partners. We are a personal injury and wellness practice. The final design should be elegant and classy, but a type of card people would want to keep. Any samples should only have Dr. Tomas Verlinde on the template.
Updates

Went on vacation/holiday

Need extra days to review

Target Market(s)

Personal Injury clients, wellness clients

Industry/Entity Type

Personal Injury, medical, wellness

Contact Information for Business Card

dr and practice name, offerings

Requirements
Must have
• Single sided, this will be printed on a transparent business card, no exceptions.

```html
<!DOCTYPE html>
<html lang="en">
<head>
<meta charset="utf-8">
<title>Brightfield Care Partners – Business Card</title>
<link rel="stylesheet" href="https://fonts.googleapis.com/css2?family=Oswald:wght@600&family=Poppins:wght@400;600&display=swap">
<style>
  :root {
    --page: #dcdcdc;
    --card-clear: #f1eeed;
    --card-clear-edge: #e4dfdd;
    --brand-blue: #0f75bc;
    --brand-orange: #f7941d;
    --brand-green: #388e45;
    --ink-light: #ffffff;
  }
  * { margin: 0; padding: 0; box-sizing: border-box; }
  html, body {
    width: 1200px;
    height: 900px;
    overflow: hidden;
    background: var(--page);
  }
  .business-card {
    position: absolute;
    left: 100px;
    top: 141px;
    width: 1000px;
    height: 618px;
    background: linear-gradient(135deg, var(--card-clear) 0%, #faf8f7 50%, var(--card-clear-edge) 100%);
    overflow: hidden;
    box-shadow: 0 10px 30px rgba(0,0,0,0.12);
  }
  .card-shapes {
    position: absolute;
    inset: 0;
    width: 100%;
    height: 100%;
  }
  .shape-green { fill: var(--brand-green); }
  .shape-orange { fill: var(--brand-orange); }
  .shape-blue { fill: var(--brand-blue); }

  .doctor-name {
    position: absolute;
    left: 59px;
    top: 132px;
    font-family: "Oswald", sans-serif;
    font-weight: 600;
    font-size: 44px;
    line-height: 1;
    letter-spacing: 0.2px;
    color: var(--brand-orange);
    text-transform: uppercase;
  }
  .name-rule {
    position: absolute;
    left: 59px;
    top: 198px;
    width: 66px;
    height: 2px;
    background: var(--ink-light);
  }
  .service-list {
    position: absolute;
    left: 59px;
    top: 256px;
    list-style: none;
  }
  .service-item {
    display: flex;
    align-items: center;
    height: 48.6px;
    font-family: "Poppins", sans-serif;
    font-weight: 400;
    font-size: 27px;
    color: var(--ink-light);
  }
  .service-bullet {
    width: 14px;
    height: 14px;
    border-radius: 50%;
    background: var(--brand-orange);
    margin: 0 22px 0 6px;
    flex: none;
  }
  .practice-mark {
    position: absolute;
    left: 500px;
    top: 500px;
    display: flex;
    align-items: center;
    gap: 14px;
  }
  .practice-dot {
    width: 26px;
    height: 26px;
    border-radius: 50%;
    background: var(--brand-orange);
    flex: none;
  }
  .practice-name {
    font-family: "Poppins", sans-serif;
    font-weight: 600;
    font-size: 29px;
    color: var(--brand-blue);
    white-space: nowrap;
  }
</style>
</head>
<body>
  <div class="business-card">
    <svg class="card-shapes" viewBox="0 0 1090 673" preserveAspectRatio="none" aria-hidden="true">
      <path class="shape-green" d="M0 0 H648 C708 170 668 430 410 673 H0 Z"/>
      <path class="shape-orange" d="M0 0 H626 C688 165 655 440 402 673 H0 Z"/>
      <path class="shape-blue" d="M0 0 H601 C662 150 640 420 366 673 H0 Z"/>
    </svg>

    <h1 class="doctor-name">Dr. Tomas Verlinde, D.C.</h1>
    <div class="name-rule"></div>

    <ul class="service-list">
      <li class="service-item"><span class="service-bullet"></span>Auto Accident Care</li>
      <li class="service-item"><span class="service-bullet"></span>Primary Care</li>
      <li class="service-item"><span class="service-bullet"></span>Medical Weight loss</li>
      <li class="service-item"><span class="service-bullet"></span>Physical Therapy</li>
      <li class="service-item"><span class="service-bullet"></span>Chiropractic</li>
    </ul>

    <div class="practice-mark">
      <span class="practice-dot"></span>
      <span class="practice-name">Brightfield Care Partners</span>
    </div>
  </div>
</body>
</html>
```